VOMRA Pty Ltd Business Card

Looking for a simple yet eye-catching double-sided business card design using my company logo on one side and contact details on the other.

Target Market(s)

Government

Industry/Entity Type

Communication Systems Engineering

Contact Information for Business Card

VOMRA Pty Ltd

Requirements
Nice to have
• Would be great to have a QR code so details can be scanned into contacts

```html
<!DOCTYPE html>
<html lang="en">
<head>
<meta charset="utf-8">
<title>VOMRA Pty Ltd Business Card</title>
<link rel="stylesheet" href="https://fonts.googleapis.com/css2?family=Open+Sans:wght@400;700&display=swap">
<style>
  :root {
    --page: #e9e7e4;
    --card: #38424a;
    --card-deep: #303940;
    --card-shade: #2b3339;
    --pattern-light: #3f4a53;
    --pattern-dark: #2a3238;
    --ink: #ffffff;
    --ink-soft: #e6eaed;
  }
  * { box-sizing: border-box; margin: 0; padding: 0; }
  html, body {
    width: 1200px; height: 780px; overflow: hidden;
    background: var(--page);
    font-family: "Open Sans", Arial, sans-serif;
  }
  .canvas { position: relative; width: 1200px; height: 780px; }
  .card {
    position: absolute; top: 70px;
    width: 380px; height: 640px;
    border-radius: 26px;
    background: var(--card);
    overflow: hidden;
    box-shadow: 0 10px 24px rgba(0,0,0,0.22);
  }
  .card--back { left: 150px; }
  .card--front { left: 670px; }

  .back-pattern {
    position: absolute; inset: 0;
    background: linear-gradient(160deg, var(--pattern-light) 0%, var(--card) 45%, var(--pattern-dark) 100%);
  }

  .front-bands { position: absolute; inset: 0; }

  .brand {
    position: absolute; top: 88px; left: 0; right: 0;
    display: flex; align-items: center; justify-content: center; gap: 18px;
  }
  .brand-mark {
    width: 22px; height: 22px; border-radius: 50%;
    background: var(--ink);
  }
  .brand-name {
    color: var(--ink); font-weight: 700; font-size: 46px; letter-spacing: 4px;
  }

  .person { position: absolute; top: 252px; left: 0; right: 0; text-align: center; color: var(--ink); }
  .person-name { font-weight: 700; font-size: 28px; line-height: 1.1; }
  .person-role { font-size: 15px; color: var(--ink-soft); margin-top: 2px; }

  .contact-icons {
    display: flex; justify-content: center; gap: 10px; margin-top: 14px;
  }
  .contact-icons svg { width: 26px; height: 26px; }

  .contact-lines { margin-top: 12px; font-size: 15px; line-height: 1.45; color: var(--ink); }

  .address {
    position: absolute; top: 520px; left: 0; right: 0;
    text-align: center; color: var(--ink); font-size: 15px; line-height: 1.45;
  }
  .address svg { width: 26px; height: 26px; display: block; margin: 0 auto 6px; }
</style>
</head>
<body>
<div class="canvas">

  <section class="card card--back">
    <div class="back-pattern" role="img" aria-label="Repeating embossed pattern of the company emblem in dark slate tones"></div>
  </section>

  <section class="card card--front">
    <svg class="front-bands" viewBox="0 0 380 640" width="380" height="640" aria-hidden="true">
      <path d="M0 380 Q40 470 190 470 Q340 470 380 360 L380 640 L0 640 Z" fill="var(--card-deep)"/>
      <path d="M0 420 Q20 500 170 505 Q320 505 380 420 L380 640 L0 640 Z" fill="var(--card-shade)" opacity="0.35"/>
      <path d="M60 640 Q150 530 380 460 L380 640 Z" fill="var(--card)"/>
    </svg>

    <div class="brand">
      <span class="brand-mark"></span>
      <span class="brand-name">VOMRA</span>
    </div>

    <div class="person">
      <h1 class="person-name">Jordan Hale</h1>
      <p class="person-role">Co-Founder</p>

      <div class="contact-icons">
        <svg viewBox="0 0 26 26" aria-label="Phone">
          <circle cx="13" cy="13" r="13" fill="var(--ink)"/>
          <path d="M9 7.5 L11 7.5 L12 10.5 L10.7 11.6 Q11.8 14 14.4 15.3 L15.5 14 L18.5 15 L18.5 17 Q18 18.5 16 18.5 Q8 17.5 7.5 9.5 Q7.5 7.8 9 7.5 Z" fill="var(--card)"/>
        </svg>
        <svg viewBox="0 0 26 26" aria-label="Email">
          <circle cx="13" cy="13" r="13" fill="var(--ink)"/>
          <rect x="7" y="8.5" width="12" height="9" rx="1" fill="var(--card)"/>
          <path d="M7.5 9 L13 13.5 L18.5 9" stroke="var(--ink)" stroke-width="1.2" fill="none"/>
        </svg>
        <svg viewBox="0 0 26 26" aria-label="Website">
          <circle cx="13" cy="13" r="13" fill="var(--ink)"/>
          <circle cx="13" cy="13" r="6" fill="none" stroke="var(--card)" stroke-width="1.5"/>
          <ellipse cx="13" cy="13" rx="2.5" ry="6" fill="none" stroke="var(--card)" stroke-width="1.2"/>
          <line x1="7" y1="13" x2="19" y2="13" stroke="var(--card)" stroke-width="1.2"/>
        </svg>
      </div>

      <div class="contact-lines">
        <p>(555) 014-2290</p>
        <p>www.vomra.com.au</p>
        <p>admin@vomra.com.au</p>
      </div>
    </div>

    <div class="address">
      <svg viewBox="0 0 26 26" aria-label="Location">
        <circle cx="13" cy="13" r="13" fill="var(--ink)"/>
        <path d="M13 6 A4.5 4.5 0 0 1 17.5 10.5 Q17.5 13.5 13 19 Q8.5 13.5 8.5 10.5 A4.5 4.5 0 0 1 13 6 Z" fill="var(--card)"/>
        <circle cx="13" cy="10.5" r="1.6" fill="var(--ink)"/>
      </svg>
      <p>42-44 Harlow Street Westbrook</p>
      <p>NSW 2999 Australia</p>
    </div>
  </section>

</div>
</body>
</html>
```